Business Card Design Project

Business Card
We are rebranding with a new logo
Industry/Entity Type
Business
Contact Information for Business Card
Dennis Morvale +61 487215963 dennis@quorv.com.au P.O. Box 872 Fernlow QLD 4309
Requirements
Must have
- Logo

```html
<!DOCTYPE html>
<html lang="en">
<head>
<meta charset="utf-8">
<title>Quorv International – Business Card</title>
<link rel="stylesheet" href="https://fonts.googleapis.com/css2?family=Play:wght@400;700&display=swap">
<style>
  :root {
    --backdrop: #e6e6e6;
    --card: #ffffff;
    --brand-blue: #1a86c7;
    --accent-orange: #f07021;
    --text-grey: #858585;
  }
  html, body {
    margin: 0;
    width: 1200px;
    height: 1000px;
    overflow: hidden;
    background: var(--backdrop);
    font-family: "Play", sans-serif;
  }
  .business-card {
    position: absolute;
    left: 221px;
    top: 277px;
    width: 760px;
    height: 432px;
    background: var(--card);
  }
  .wordmark {
    position: absolute;
    right: 46px;
    top: 52px;
    text-align: right;
    color: var(--brand-blue);
    font-weight: 700;
    line-height: 1;
  }
  .wordmark-name {
    display: block;
    font-size: 66px;
    letter-spacing: 1px;
  }
  .wordmark-sub {
    display: block;
    margin-top: 10px;
    font-size: 17px;
    letter-spacing: 3.6px;
  }
  .holder-name {
    position: absolute;
    left: 47px;
    top: 276px;
    margin: 0;
    font-size: 21px;
    font-weight: 400;
    letter-spacing: 0.6px;
    color: var(--brand-blue);
  }
  .name-rule {
    position: absolute;
    left: 47px;
    top: 311px;
    width: 16px;
    height: 2px;
    background: var(--brand-blue);
  }
  .contact-list {
    position: absolute;
    left: 47px;
    top: 333px;
    margin: 0;
    padding: 0;
    list-style: none;
    font-size: 16px;
    color: var(--text-grey);
    letter-spacing: 0.3px;
  }
  .contact-list li {
    display: flex;
    align-items: center;
    height: 24px;
  }
  .contact-icon {
    width: 16px;
    margin-right: 17px;
    display: flex;
    justify-content: center;
  }
  .postal-address {
    position: absolute;
    left: 543px;
    top: 333px;
    margin: 0;
    font-style: normal;
    font-size: 16px;
    line-height: 24px;
    color: var(--text-grey);
    letter-spacing: 0.3px;
  }
  .accent-bar {
    position: absolute;
    left: 543px;
    bottom: 0;
    width: 170px;
    height: 12px;
    background: var(--accent-orange);
  }
</style>
</head>
<body>
  <section class="business-card">
    <div class="wordmark">
      <span class="wordmark-name">Quorv</span>
      <span class="wordmark-sub">INTERNATIONAL</span>
    </div>

    <h1 class="holder-name">DENNIS MORVALE</h1>
    <div class="name-rule"></div>

    <ul class="contact-list">
      <li>
        <span class="contact-icon">
          <svg width="10" height="15" viewBox="0 0 10 15" aria-hidden="true">
            <rect x="1" y="1" width="8" height="13" rx="1.5" fill="none" stroke="#f07021" stroke-width="1.6"/>
            <rect x="4" y="11" width="2" height="1.4" fill="#f07021"/>
          </svg>
        </span>
        +61 487215963
      </li>
      <li>
        <span class="contact-icon">
          <svg width="14" height="11" viewBox="0 0 14 11" aria-hidden="true">
            <rect x="0" y="0" width="14" height="11" rx="1" fill="#f07021"/>
            <path d="M0.5 1 L7 6 L13.5 1" fill="none" stroke="#ffffff" stroke-width="1.2"/>
          </svg>
        </span>
        dennis@quorv.com.au
      </li>
    </ul>

    <address class="postal-address">
      P.O. Box 872<br>
      Fernlow QLD 4309
    </address>

    <div class="accent-bar"></div>
  </section>
</body>
</html>
```